Create banner ads for a digital product that deletes personal information from the web

The context of the banners is general advertisement for our service.
Please provide us with a set of static and flash/gif banners in the following standard sizes for the theme you create:
160x600
300x250
300x600
320x250
336x280
728x90
Please see our website for logo (just our name) and theme ideas - please follow similar color/font schemes if possible. www.quillbranchdata.com
Our company is an online service that deletes personal information from the internet for our members (automated opt-outs and content removal). Our target audience is anyone who wishes to protect their personal information from being on the internet (i.e. prefer to fly under the internet radar, for example). This is a product for U.S. residents who value privacy and online reputation. We seek to provide members with control of what 300+ websites are sharing about them – removing names, addresses, ages, phone numbers, email addresses, children’s information, home/property value information etc.
Internet

```html
<!DOCTYPE html>
<html lang="en">
<head>
<meta charset="utf-8">
<title>QuillBranchData – Personal Privacy Banner</title>
<link rel="stylesheet" href="https://fonts.googleapis.com/css2?family=Arimo:wght@400;700&display=swap">
<style>
  :root {
    --sky-pale: #f6ecc0;
    --sky-gold: #e9c86a;
    --sun-glow: #fff8dc;
    --sky-amber: #d7b15c;
    --sky-dusk: #8d9cab;
    --sky-blue: #6f8aa6;
    --ink: #15151f;
    --logo: #ffffff;
  }
  html, body {
    margin: 0;
    padding: 0;
    overflow: hidden;
    background: #ffffff;
  }
  .banner {
    position: relative;
    width: 1200px;
    height: 148px;
    overflow: hidden;
    font-family: "Arimo", Arial, sans-serif;
  }
  .banner__scene {
    position: absolute;
    inset: 0;
    background:
      radial-gradient(ellipse 320px 120px at 560px 95px, var(--sun-glow) 0%, rgba(255,248,220,0.6) 35%, rgba(255,248,220,0) 75%),
      radial-gradient(ellipse 260px 90px at 1120px 40px, rgba(111,138,166,0.9) 0%, rgba(111,138,166,0) 100%),
      linear-gradient(90deg, var(--sky-pale) 0%, var(--sky-gold) 30%, var(--sky-amber) 52%, var(--sky-dusk) 75%, var(--sky-blue) 100%);
  }
  .banner__headline {
    position: absolute;
    left: 41px;
    top: 20px;
    margin: 0;
    font-size: 50px;
    font-weight: 400;
    letter-spacing: -0.5px;
    color: var(--ink);
    line-height: 1;
  }
  .banner__subline {
    position: absolute;
    left: 190px;
    top: 86px;
    margin: 0;
    font-size: 34px;
    font-weight: 400;
    color: var(--ink);
    line-height: 1;
  }
  .banner__brand {
    position: absolute;
    left: 957px;
    top: 90px;
    margin: 0;
    font-size: 34px;
    font-weight: 400;
    color: var(--logo);
    line-height: 1;
  }
</style>
</head>
<body>
  <div class="banner">
    <div class="banner__scene" role="img" aria-label="Golden sunset sky with soft clouds and a man in a white shirt raising his arms toward the light"></div>
    <h1 class="banner__headline">Your Personal Privacy</h1>
    <p class="banner__subline">is threatened daily</p>
    <p class="banner__brand">QuillBranchData</p>
  </div>
</body>
</html>
```